Kelvara Pane Works Business Card

We need a business card design that is suitable for a Glazing Business. We Specialize in Repairing broken windows and doors and are a 24hr on call service. We manufacture Shower screens, Fly screens, Wardrobe doors, Security doors and grilles + mirrors. We stock a variety of mesh including Standard mesh, Pet resistant mesh, Tressmet & Clearweft. We would like to use a combination of Light Blue, Dark Blue, Black & White with perhaps a picture of glass breaking.

Industry/Entity Type

Business

Contact Information for Business Card

Narooma Glass Service60B Glasshouse Rocks RdNarooma NSW 2546PH / FAX - 02 44765210MOB - 0419682350 Andrewemail - kelvarapane@fenmail.example

Font styles to use
Serif

Colors
34a7d8
0255a3
ffffff

Requirements
Must have
• logo with picture of broken or cracked glass

```html
<!DOCTYPE html>
<html lang="en">
<head>
<meta charset="utf-8">
<title>Kelvara Pane Works Business Card</title>
<link rel="stylesheet" href="https://fonts.googleapis.com/css2?family=Source+Sans+3:wght@400;600&display=swap">
<style>
  :root {
    --backdrop: #3b3430;
    --card: #0b0b0c;
    --blue: #1a66e8;
    --ice: #34a7d8;
    --white: #ffffff;
    --shadow: rgba(0,0,0,0.55);
  }
  * { box-sizing: border-box; margin: 0; padding: 0; }
  html, body {
    width: 1200px; height: 844px; overflow: hidden;
    background: var(--backdrop);
    font-family: "Source Sans 3", "Myriad Pro", sans-serif;
    color: var(--white);
  }
  .stage { position: relative; width: 1200px; height: 844px; }
  .card {
    position: absolute; top: 264px;
    width: 520px; height: 316px;
    background: var(--card);
    border-radius: 4px;
    box-shadow: 0 14px 30px var(--shadow);
  }
  .card--front { left: 50px; }
  .card--back { left: 630px; }

  .brand { position: absolute; display: flex; align-items: center; gap: 10px; }
  .brand__mark {
    width: 62px; height: 62px;
    background: linear-gradient(135deg, #bfe6f6, var(--ice) 55%, var(--blue));
    flex: none;
  }
  .brand__name {
    color: var(--blue); font-weight: 400;
    line-height: 1; text-transform: uppercase;
  }
  .brand__line1 { display: block; font-size: 40px; letter-spacing: 0.5px; }
  .brand__line2 { display: block; font-size: 22px; letter-spacing: 5px; margin-top: 2px; }
  .card--front .brand { left: 48px; top: 62px; }
  .card--back .brand { left: 94px; top: 76px; }

  .contact {
    position: absolute; right: 278px; top: 176px;
    list-style: none; text-align: right;
    font-size: 15px; line-height: 22px;
  }
  .contact li { display: flex; justify-content: flex-end; align-items: center; gap: 6px; }
  .contact svg { width: 11px; height: 11px; fill: var(--blue); flex: none; }
  .contact .contact__email { margin-right: 0; }

  .person { position: absolute; left: 290px; top: 150px; }
  .person__name { color: var(--blue); font-weight: 600; font-size: 18px; margin-bottom: 10px; }
  .person__address { font-style: normal; font-size: 14px; line-height: 21px; }

  .services {
    position: absolute; left: 0; right: 0; top: 176px;
    text-align: center; font-size: 15px; line-height: 22px;
  }
  .services .dot {
    display: inline-block; width: 6px; height: 6px; border-radius: 50%;
    background: var(--blue); margin: 0 7px 2px; vertical-align: middle;
  }
</style>
</head>
<body>
<main class="stage">

  <section class="card card--front" aria-label="Card front">
    <div class="brand">
      <span class="brand__mark" role="img" aria-label="Cracked glass logo area"></span>
      <span class="brand__name">
        <span class="brand__line1">Kelvara</span>
        <span class="brand__line2">Pane Works</span>
      </span>
    </div>

    <ul class="contact">
      <li>02 48931067
        <svg viewBox="0 0 12 12"><path d="M2 1l2 0 1 3-1.3 1a6 6 0 0 0 3.3 3.3L8 7l3 1v2c0 .6-.5 1-1 1C5 11 1 7 1 2c0-.5.4-1 1-1z"/></svg></li>
      <li>02 48931067
        <svg viewBox="0 0 12 12"><path d="M3 1h5v3H3zM1 5h10v6H1zm2 2v1h2V7zm4 0v1h2V7z"/></svg></li>
      <li>0419682350
        <svg viewBox="0 0 12 12"><path d="M3 0h6a1 1 0 0 1 1 1v10a1 1 0 0 1-1 1H3a1 1 0 0 1-1-1V1a1 1 0 0 1 1-1zm0 2v7h6V2z"/></svg></li>
      <li class="contact__email">kelvarapane@fenmail.example
        <svg viewBox="0 0 12 12"><path d="M0 2h12v8H0zm1 1v.4l5 3.2 5-3.2V3z"/></svg></li>
    </ul>

    <div class="person">
      <p class="person__name">Malcolm</p>
      <address class="person__address">17C Tindale Ridge<br>Rd Kelvara NSW 2611</address>
    </div>
  </section>

  <section class="card card--back" aria-label="Card back">
    <div class="brand">
      <span class="brand__mark" role="img" aria-label="Cracked glass logo area"></span>
      <span class="brand__name">
        <span class="brand__line1">Kelvara</span>
        <span class="brand__line2">Pane Works</span>
      </span>
    </div>

    <div class="services">
      <p>Shower screens<span class="dot"></span>Fly screens<span class="dot"></span>Wardrobe doors</p>
      <p>Security doors<span class="dot"></span>Grilles + mirrors</p>
    </div>
  </section>

</main>
</body>
</html>
```